Harrow Tavern & Grille Menu Makeover

I am looking for a professional look to update our current menu. We are an independently owned sports bar and grill. Up to this point, I have done all of my own graphic designing. I am looking for something classy/family oriented. We are a very family friendly sports bar that offers a wide variety of menu options. Our website is www.harrowtavernco.example. This may help you get more of a feel for what type of place we are and what we offer. Our menu is listed on the website. My current menu is 8.5x14 inserts that feature a cover page, 4 inside pages and a back page. I would like something a little more condensed than this. Possibly a large tri-fold menu? I am open to all new ideas. I do have some pictures on my menu now, and would like to continue using a few pictures to feature some of my items. I would like something that is in a format that gives me the option to change items and prices on my own in the future. I would also like it to feature, or inform my patrons about our technology that we offer. We offer online ordering and we are a "verified venue" with Brewvoke.( a social site for craft beer lovers).

Industry/Entity Type

Sports Bar

Requirements
Nice to have
• Nice to have some pictures, but does not have to. We do feature 9 different beers on tap. A lot of them are local craft beers from the state of Kansas. Not sure if that is something we can feature, but it is a nice talking point. All of our tables and bar are hand built. With a rich mahogany finish on all of our woodwork, some type of "woodgrain" look into the menu would be nice.

```html
<!DOCTYPE html>
<html lang="en">
<head>
<meta charset="utf-8">
<title>Harrow Tavern &amp; Grille — Menu</title>
<link rel="stylesheet" href="https://fonts.googleapis.com/css2?family=Cinzel:wght@500;600&family=Oswald:wght@400;500&family=Roboto+Condensed:wght@300;400&display=swap">
<style>
  :root {
    --ink: #0b0a09;
    --panel: rgba(14, 13, 12, 0.93);
    --gold: #c9a55a;
    --gold-soft: #8f7543;
    --item: #f2efe8;
    --desc: #9c978e;
    --photo-warm: #a8742e;
    --photo-deep: #4a2e14;
  }
  * { margin: 0; padding: 0; box-sizing: border-box; }
  html, body { width: 851px; height: 1200px; overflow: hidden; background: var(--ink); }
  .menu-page { position: relative; width: 851px; height: 1200px; overflow: hidden; background: var(--ink); }
  .hero-photo {
    position: absolute; inset: 0 0 auto 0; height: 620px;
    background:
      radial-gradient(ellipse at 50% 12%, #d8a95a 0%, var(--photo-warm) 25%, var(--photo-deep) 55%, transparent 80%),
      linear-gradient(180deg, #7a5024 0%, #3a2410 45%, var(--ink) 100%);
  }
  .menu-panel {
    position: absolute; left: 66px; top: 208px; width: 720px; height: 915px;
    background: var(--panel); border-radius: 14px;
    box-shadow: 0 10px 40px rgba(0,0,0,.6);
  }
  .section-title {
    position: absolute; left: 97px;
    font-family: "Cinzel", serif; font-weight: 500; font-size: 27px;
    letter-spacing: 1px; color: var(--gold);
  }
  .item-grid {
    position: absolute; left: 97px; width: 660px;
    display: grid; grid-template-columns: 300px 300px; column-gap: 30px;
  }
  .item-column { display: flex; flex-direction: column; gap: 13px; }
  .item-name {
    font-family: "Oswald", sans-serif; font-weight: 500; font-size: 12.5px;
    text-transform: uppercase; letter-spacing: .4px; color: var(--item); line-height: 1.2;
  }
  .item-desc {
    font-family: "Roboto Condensed", sans-serif; font-weight: 300; font-size: 8px;
    text-transform: uppercase; letter-spacing: .3px; color: var(--desc);
    line-height: 1.35; margin-top: 2px; width: 290px;
  }
  .section-divider { position: absolute; left: 97px; width: 660px; height: 14px; }
</style>
</head>
<body>
<main class="menu-page">
  <div class="hero-photo" role="img" aria-label="Photograph of a burger with golden curly fries"></div>

  <section class="menu-panel" aria-label="Menu"></section>

  <h2 class="section-title" style="top:236px">Burgers</h2>
  <div class="item-grid" style="top:283px">
    <div class="item-column">
      <div><h3 class="item-name">Black Angus Blue Cheese &amp; Bacon Burger</h3><p class="item-desc">A half pound Angus patty with crumbled blue cheese, crisp bacon, lettuce, tomato and onion on a toasted bun.</p></div>
      <div><h3 class="item-name">All-American Cheeseburger</h3><p class="item-desc">A half pound Angus patty topped with American cheese, lettuce, tomato and pickles.</p></div>
      <div><h3 class="item-name">San Francisco Burger</h3><p class="item-desc">A half pound patty on grilled sourdough with Swiss cheese, sautéed onions and thousand island.</p></div>
      <div><h3 class="item-name">French Dip Burger</h3><p class="item-desc">A half pound patty topped with sautéed onions and Swiss on a hoagie, served with warm au jus.</p></div>
      <div><h3 class="item-name">Gourmet Patty Melt</h3><p class="item-desc">A half pound patty with Swiss and American cheese and grilled onions on toasted rye.</p></div>
    </div>
    <div class="item-column">
      <div><h3 class="item-name">Harrow Double Bacon Cheeseburger</h3><p class="item-desc">Two quarter pound patties stacked with bacon and American cheese, lettuce, tomato and onion.</p></div>
      <div><h3 class="item-name">Quesadilla Burger</h3><p class="item-desc">A crispy flour tortilla stuffed with a seasoned patty, pepper jack, pico de gallo and chipotle ranch.</p></div>
      <div><h3 class="item-name">Pepper Jack Cheeseburger</h3><p class="item-desc">A half pound patty topped with pepper jack cheese, grilled jalapeños and chipotle mayo.</p></div>
      <div><h3 class="item-name">Texas Burger</h3><p class="item-desc">A half pound patty topped with BBQ sauce, cheddar, onion rings and bacon.</p></div>
      <div><h3 class="item-name">Bourbon Burger</h3><p class="item-desc">A half pound patty glazed with bourbon sauce, smoked cheddar and crispy onions.</p></div>
    </div>
  </div>

  <svg class="section-divider" style="top:598px" viewBox="0 0 660 14" aria-hidden="true">
    <line x1="170" y1="7" x2="312" y2="7" stroke="var(--gold-soft)" stroke-width="1"/>
    <line x1="348" y1="7" x2="490" y2="7" stroke="var(--gold-soft)" stroke-width="1"/>
    <rect x="325" y="2" width="10" height="10" fill="none" stroke="var(--gold)" stroke-width="1.2" transform="rotate(45 330 7)"/>
  </svg>

  <h2 class="section-title" style="top:640px">Pasta</h2>
  <div class="item-grid" style="top:688px">
    <div class="item-column">
      <div><h3 class="item-name">Lasagna</h3><p class="item-desc">Layers of pasta, meat sauce and three cheeses, baked and served with garlic toast.</p></div>
      <div><h3 class="item-name">Italian Sausage &amp; Meatballs</h3><p class="item-desc">Spaghetti tossed in marinara with house meatballs and Italian sausage, topped with parmesan.</p></div>
    </div>
    <div class="item-column">
      <div><h3 class="item-name">Fettuccine Alfredo</h3><p class="item-desc">Fettuccine noodles tossed in our creamy alfredo sauce, served with garlic toast. Add chicken or shrimp.</p></div>
      <div><h3 class="item-name">Chicken Parmesan</h3><p class="item-desc">Breaded chicken breast topped with marinara and mozzarella over a bed of spaghetti.</p></div>
    </div>
  </div>

  <svg class="section-divider" style="top:778px" viewBox="0 0 660 14" aria-hidden="true">
    <line x1="170" y1="7" x2="312" y2="7" stroke="var(--gold-soft)" stroke-width="1"/>
    <line x1="348" y1="7" x2="490" y2="7" stroke="var(--gold-soft)" stroke-width="1"/>
    <rect x="325" y="2" width="10" height="10" fill="none" stroke="var(--gold)" stroke-width="1.2" transform="rotate(45 330 7)"/>
  </svg>

  <h2 class="section-title" style="top:808px">Mexican</h2>
  <div class="item-grid" style="top:855px">
    <div class="item-column">
      <div><h3 class="item-name">Taco Bowl</h3><p class="item-desc">A crispy tortilla bowl filled with seasoned beef, lettuce, cheese, tomato, sour cream and salsa.</p></div>
      <div><h3 class="item-name">Six Pack Tacos</h3><p class="item-desc">Six soft or crispy tacos with seasoned beef, lettuce, cheese and tomato.</p></div>
      <div><h3 class="item-name">Chimichanga</h3><p class="item-desc">A deep fried flour tortilla stuffed with beef or chicken, smothered in queso, with rice and beans.</p></div>
    </div>
    <div class="item-column">
      <div><h3 class="item-name">Southwest Chicken Sancho</h3><p class="item-desc">Grilled chicken, black beans, corn and pepper jack wrapped in a flour tortilla with salsa.</p></div>
      <div><h3 class="item-name">Loaded Chicken Quesadilla</h3><p class="item-desc">Chicken, bacon, cheddar and jack cheese with peppers and onions, served with salsa and sour cream.</p></div>
    </div>
  </div>
</main>
</body>
</html>
```